Dynamic Business Card for Sports Supplements Company

Hi! I'm looking for an awesome business card to match my existing sports supplement company. I have uploaded my current company logo and screenshot of the front page of my website.

I would like to have something dynamic and interesting and utilize the colors in the website - the reds and purples

The business card should be double sided and focus on a unique eye-catching design on the back and include all the relevant company info.

Most importantly, it should say somewhere: "Sign up on our website for a coupon code."

Target Market(s)

Mostly for women gym goers but it shouldn't be too feminine. It should be in keeping with the website design. It should flow and clearly be connected to it

Industry/Entity Type

Business

Contact Information for Business Card

Lorraine K. Vestal
CEO
LVestal@Quorvanexco.com
www.quorvanexco.com
555.417.3820
P.O. Box 47315
Linden Vale, Westmark 00000

Sign up on our website for a coupon code

Font styles to use
Serif
Sans Serif
Other font styles liked:
• Novecento font family and "Quorvanex" is in AR Destine font

Requirements
Must have
• One side should be a bold Quorvanex logo design. Even just the symbol itself may be o.k. (see attached file)

```html
<!DOCTYPE html>
<html lang="en">
<head>
<meta charset="utf-8">
<title>Quorvanex Business Card</title>
<link rel="stylesheet" href="https://fonts.googleapis.com/css2?family=Source+Sans+3:ital,wght@0,400;0,600;0,700;1,400&display=swap">
<style>
  :root {
    --stage: #e9e6e2;
    --card-black: #000000;
    --brand-red: #ed1c24;
    --paper-white: #ffffff;
    --text-light: #f2f2f2;
    --muted-grey: #6d6d6d;
    --divider: #3a3a3a;
    --pattern-dark: #1c1a1b;
    --pattern-red: #2a1416;
  }
  * { box-sizing: border-box; margin: 0; padding: 0; }
  html, body {
    width: 1200px; height: 987px; overflow: hidden;
    background: var(--stage);
    font-family: "Source Sans 3", Arial, sans-serif;
  }
  .stage { position: relative; width: 1200px; height: 987px; }
  .card {
    position: absolute; left: 293px; width: 615px; height: 350px;
    overflow: hidden; background: var(--card-black);
    box-shadow: 0 6px 14px rgba(0,0,0,0.25);
  }
  .card--front { top: 129px; }
  .card--back { top: 506px; }
  .card__shapes { position: absolute; inset: 0; }

  .brand-lockup {
    position: absolute; left: 0; width: 300px; top: 160px;
    text-align: center;
  }
  .brand-lockup__mark {
    display: block; width: 36px; height: 36px; margin: 0 auto 10px;
    background: var(--brand-red);
  }
  .brand-lockup__name {
    color: var(--paper-white); font-weight: 700; font-size: 34px;
    letter-spacing: 2px; line-height: 1; text-transform: uppercase;
  }
  .brand-lockup__tagline {
    color: var(--muted-grey); font-size: 10px; letter-spacing: 2.6px;
    text-transform: uppercase; margin-top: 4px;
  }
  .divider {
    position: absolute; left: 299px; top: 88px; width: 1px; height: 182px;
    background: var(--divider);
  }
  .contact { position: absolute; left: 321px; top: 80px; color: var(--text-light); }
  .contact__name {
    color: var(--brand-red); font-size: 22px; font-weight: 600;
    text-transform: uppercase; line-height: 1.1;
  }
  .contact__role { font-size: 17px; margin: 2px 0 12px 3px; }
  .contact__address { font-size: 16.5px; line-height: 23px; margin-left: 3px; }
  .contact__list { list-style: none; margin-top: 4px; }
  .contact__item {
    display: flex; align-items: center; gap: 7px;
    font-size: 16.5px; line-height: 23px; margin-left: 3px;
  }
  .contact__icon { width: 13px; height: 13px; flex: none; fill: var(--brand-red); }

  .back-pattern {
    position: absolute; inset: 0;
    background: linear-gradient(180deg, var(--pattern-dark), var(--pattern-red) 50%, var(--pattern-dark));
  }
  .back-brand {
    position: absolute; left: 0; right: 0; top: 152px; text-align: center;
  }
  .back-brand__name {
    color: var(--paper-white); font-weight: 700; font-size: 30px;
    letter-spacing: 1px; text-transform: uppercase;
  }
  .back-offer {
    position: absolute; left: 0; right: 0; top: 277px; text-align: center;
    color: var(--paper-white); font-style: italic; font-size: 17px;
  }
</style>
</head>
<body>
<main class="stage">
  <section class="card card--front" aria-label="Business card front">
    <svg class="card__shapes" viewBox="0 0 615 350" width="615" height="350" aria-hidden="true">
      <polygon points="0,0 615,0 615,2 0,41" fill="var(--brand-red)"/>
      <polygon points="0,350 615,311 615,350" fill="var(--paper-white)"/>
    </svg>
    <div class="brand-lockup">
      <span class="brand-lockup__mark"></span>
      <div class="brand-lockup__name">Quorvanex</div>
      <div class="brand-lockup__tagline">Your Training Companion</div>
    </div>
    <div class="divider"></div>
    <div class="contact">
      <h1 class="contact__name">Lorraine K. Vestal</h1>
      <p class="contact__role">CEO</p>
      <p class="contact__address">P.O. Box 47315<br>Linden Vale, Westmark 00000</p>
      <ul class="contact__list">
        <li class="contact__item">
          <svg class="contact__icon" viewBox="0 0 16 16"><path d="M3.5 1l2.5 3-1.5 2c1 2 3 4 5 5l2-1.5 3 2.5-1.5 2.5C7 14 2 9 1 2.5z"/></svg>
          555.417.3820
        </li>
        <li class="contact__item">
          <svg class="contact__icon" viewBox="0 0 16 16"><path d="M1 3h14v2L8 9 1 5z"/><path d="M1 6.5l7 4 7-4V13H1z"/></svg>
          LVestal@Quorvanexco.com
        </li>
        <li class="contact__item">
          <svg class="contact__icon" viewBox="0 0 16 16"><circle cx="8" cy="8" r="7"/><path d="M1 8h14M8 1c-3 3-3 11 0 14M8 1c3 3 3 11 0 14" stroke="#000" stroke-width="1.2" fill="none"/></svg>
          www.quorvanexco.com
        </li>
      </ul>
    </div>
  </section>

  <section class="card card--back" aria-label="Business card back">
    <div class="back-pattern" role="img" aria-label="Repeating dark chevron pattern in charcoal and deep red"></div>
    <div class="back-brand"><span class="back-brand__name">Quorvanex</span></div>
    <p class="back-offer">Sign up on our website for a coupon code</p>
  </section>
</main>
</body>
</html>
```